Business Card Design for Software Development Company

I am looking for a business card design the incorporates my new logo (attached below).

Key information to include:
Name: Martin Quelbrook
Title: CEO
Email: martin@brightwellcivic.example
Phone: 555-218-9403
Website: www.brightwellcivic.example

NOTE: This design should be easy to edit so that we can order cards for different members of our team.

```html
<!DOCTYPE html>
<html lang="en">
<head>
<meta charset="utf-8">
<title>BrightwellLabs – Business Card</title>
<link rel="stylesheet" href="https://fonts.googleapis.com/css2?family=Montserrat:wght@400;500;600;700&display=swap">
<style>
  :root {
    --backdrop: #2a2a2a;
    --card: #ffffff;
    --ink: #1f1f1f;
    --muted: #3a3a3a;
    --teal: #1aae9f;
    --orange: #ee7a2a;
  }
  * { box-sizing: border-box; margin: 0; padding: 0; }
  html, body {
    width: 1200px; height: 900px; overflow: hidden;
    background: var(--backdrop);
    font-family: "Montserrat", Arial, sans-serif;
  }
  .sheet {
    width: 1200px; height: 900px;
    display: flex; flex-direction: column; align-items: center; justify-content: center;
    gap: 34px;
  }
  .card {
    position: relative;
    width: 700px; height: 400px;
    background: var(--card);
    border-bottom: 6px solid var(--teal);
    box-shadow: 0 10px 24px rgba(0,0,0,.45);
  }
  .wordmark { display: flex; align-items: flex-start; gap: 10px; }
  .wordmark-square { background: var(--orange); flex: none; }
  .wordmark-text { display: flex; flex-direction: column; align-items: flex-end; }
  .wordmark-name {
    color: var(--ink); font-weight: 600; letter-spacing: -0.5px; line-height: 1;
  }
  .wordmark-tagline {
    color: var(--ink); font-weight: 700; text-transform: uppercase; letter-spacing: .6px;
    margin-top: 4px;
  }

  /* front */
  .card--front { display: flex; align-items: center; justify-content: center; }
  .card--front .wordmark-square { width: 34px; height: 34px; margin-top: 10px; }
  .card--front .wordmark-name { font-size: 56px; }
  .card--front .wordmark-tagline { font-size: 10px; }

  /* back */
  .card--back { display: flex; align-items: center; padding: 0 40px 0 56px; }
  .card--back .wordmark { width: 310px; }
  .card--back .wordmark-square { width: 18px; height: 18px; margin-top: 6px; }
  .card--back .wordmark-name { font-size: 29px; }
  .card--back .wordmark-tagline { font-size: 6px; margin-top: 3px; }
  .divider { width: 1px; height: 170px; background: var(--teal); margin: 0 24px 0 14px; }
  .contact { display: flex; flex-direction: column; }
  .person-name { font-size: 25px; font-weight: 700; line-height: 1.1; letter-spacing: .3px; }
  .person-name .first { color: var(--teal); }
  .person-name .last { color: var(--orange); }
  .person-title { font-size: 15px; color: var(--muted); font-weight: 400; margin: 2px 0 16px 6px; }
  .contact-list { list-style: none; display: flex; flex-direction: column; gap: 8px; }
  .contact-item {
    display: flex; align-items: center; gap: 8px;
    font-size: 14px; color: var(--muted); font-weight: 400;
  }
  .contact-icon { width: 13px; height: 13px; flex: none; fill: var(--orange); }
</style>
</head>
<body>
<main class="sheet">
  <section class="card card--front" aria-label="Card front">
    <div class="wordmark">
      <span class="wordmark-square" aria-hidden="true"></span>
      <div class="wordmark-text">
        <span class="wordmark-name">BrightwellLabs</span>
        <span class="wordmark-tagline">A division of Brightwell Civic</span>
      </div>
    </div>
  </section>

  <section class="card card--back" aria-label="Card back">
    <div class="wordmark">
      <span class="wordmark-square" aria-hidden="true"></span>
      <div class="wordmark-text">
        <span class="wordmark-name">BrightwellLabs</span>
        <span class="wordmark-tagline">A division of Brightwell Civic</span>
      </div>
    </div>
    <span class="divider" aria-hidden="true"></span>
    <div class="contact">
      <h1 class="person-name"><span class="first">Martin</span> <span class="last">Quelbrook</span></h1>
      <p class="person-title">CEO</p>
      <ul class="contact-list">
        <li class="contact-item">
          <svg class="contact-icon" viewBox="0 0 16 16" aria-hidden="true"><path d="M3 1h3l1.5 4-2 1.3a9 9 0 0 0 4.2 4.2L11 8.5 15 10v3a2 2 0 0 1-2 2A12 12 0 0 1 1 3a2 2 0 0 1 2-2z"/></svg>
          555-218-9403
        </li>
        <li class="contact-item">
          <svg class="contact-icon" viewBox="0 0 16 16" aria-hidden="true"><path d="M1 3h14v10H1z M2 4l6 5 6-5" fill="none" stroke="#ee7a2a" stroke-width="1.6"/></svg>
          martin@brightwellcivic.example
        </li>
        <li class="contact-item">
          <svg class="contact-icon" viewBox="0 0 16 16" aria-hidden="true"><circle cx="8" cy="8" r="6.5" fill="none" stroke="#ee7a2a" stroke-width="1.5"/><path d="M1.5 8h13M8 1.5c-3 3.5-3 9.5 0 13M8 1.5c3 3.5 3 9.5 0 13" fill="none" stroke="#ee7a2a" stroke-width="1.2"/></svg>
          www.brightwellcivic.example
        </li>
      </ul>
    </div>
  </section>
</main>
</body>
</html>
```